dsadasdasdasdsa

Industry/Entity Type

Mortgage Broking

Requirements
Must have
• Call-to-action button somewhere on the graphic
Nice to have
• The font of our logo is Montserrat

```html
<!DOCTYPE html>
<html lang="en">
<head>
<meta charset="UTF-8">
<title>Mortgage Broker Directory Banner</title>
<link rel="stylesheet" href="https://fonts.googleapis.com/css2?family=Montserrat:wght@700;800;900&display=swap">
<style>
  :root {
    --bg-deep: #0c4a22;
    --bg-mid: #17703a;
    --frame: #ffffff;
    --cta-red: #b8321f;
    --cta-orange: #c9462a;
    --panel-green: #0f5a2c;
    --panel-green-light: #1a8a4c;
    --yellow: #f4f526;
    --mint: #3fe6a2;
    --white: #ffffff;
  }
  * { box-sizing: border-box; margin: 0; padding: 0; }
  html, body {
    width: 1200px;
    height: 180px;
    overflow: hidden;
  }
  body {
    font-family: "Montserrat", sans-serif;
    background: var(--bg-deep);
  }
  .banner {
    position: relative;
    width: 1200px;
    height: 180px;
    overflow: hidden;
    background:
      repeating-conic-gradient(from 0deg at 50% 50%, rgba(255,255,255,0.04) 0deg 6deg, rgba(0,0,0,0) 6deg 14deg),
      radial-gradient(ellipse at 50% 50%, var(--bg-mid) 0%, var(--bg-deep) 75%);
  }
  .banner__frame {
    position: absolute;
    left: 21px;
    top: 14px;
    width: 1158px;
    height: 157px;
    background: var(--frame);
    border-radius: 26px;
  }
  .banner__panel {
    position: absolute;
    left: 41px;
    top: 29px;
    width: 1124px;
    height: 126px;
    border-radius: 12px;
    background: linear-gradient(90deg,
      var(--cta-red) 0%,
      var(--cta-orange) 24%,
      var(--panel-green) 40%,
      var(--panel-green) 62%,
      var(--panel-green-light) 100%);
  }
  .cta-button {
    position: absolute;
    left: 60px;
    top: 70px;
    width: 176px;
    height: 43px;
    border: 2px solid var(--white);
    border-radius: 22px;
    display: flex;
    align-items: center;
    justify-content: center;
    color: var(--yellow);
    font-weight: 800;
    font-size: 17px;
    letter-spacing: 0.2px;
    text-decoration: none;
  }
  .mascot {
    position: absolute;
    left: 240px;
    top: 2px;
    width: 190px;
    height: 176px;
    border-radius: 46% 46% 38% 38%;
    background: radial-gradient(ellipse at 45% 40%, #7fcf6a 0%, #4a9a45 45%, #7a4a2a 100%);
    opacity: 0.95;
  }
  .message {
    position: absolute;
    left: 494px;
    top: 38px;
  }
  .message__lead {
    color: var(--yellow);
    font-weight: 700;
    font-size: 28px;
    line-height: 1;
    margin-bottom: 14px;
  }
  .message__headline {
    color: var(--mint);
    font-weight: 900;
    font-size: 33px;
    line-height: 1;
    text-transform: uppercase;
    letter-spacing: 0.2px;
  }
  .message__headline span { display: block; margin-bottom: 4px; }
</style>
</head>
<body>
  <div class="banner">
    <div class="banner__frame"></div>
    <div class="banner__panel"></div>
    <a class="cta-button" href="#">CLICK HERE</a>
    <div class="mascot" role="img" aria-label="Cartoon turtle mascot holding a small house"></div>
    <div class="message">
      <p class="message__lead">Need a Mortgage Broker?</p>
      <h1 class="message__headline">
        <span>Search now on Australia’s</span>
        <span>Largest Directory</span>
      </h1>
    </div>
  </div>
</body>
</html>
```